Design a New Business Card for Our Company

We are looking for fresh, unique, and a modern business card that reflects our roots as digital marketing agency focused on SEM.

Industry/Entity Type

Marketing

Contact Information for Business Card

looking for very unique out of the box designs. clean and modern that compliments our logo

Requirements
Must have
• colors should match our logo
• Front should have name, address, email, and phone/fax of the person, phone/fax are the same number
• back should have our url

```html
<!DOCTYPE html>
<html lang="en">
<head>
<meta charset="utf-8">
<title>Brightpath Labs Business Card</title>
<link rel="stylesheet" href="https://fonts.googleapis.com/css2?family=Montserrat:wght@400;500;600;700&display=swap">
<style>
  :root {
    --blue: #5b9bd5;
    --grey: #a9a9a9;
    --grey-light: #cfcfcf;
    --grey-text: #9a9a9a;
    --white: #ffffff;
    --backdrop: #e9ebee;
  }
  * { margin: 0; padding: 0; box-sizing: border-box; }
  html, body { width: 1200px; height: 900px; overflow: hidden; }
  body {
    background: var(--backdrop);
    font-family: "Montserrat", Arial, sans-serif;
    position: relative;
  }
  .card {
    position: absolute;
    left: 280px;
    width: 640px;
    height: 366px;
    background: var(--white);
    border-radius: 18px;
    overflow: hidden;
    box-shadow: 0 6px 18px rgba(0,0,0,0.12);
  }
  .card-back { top: 46px; }
  .card-front { top: 488px; }
  .card .bands { position: absolute; inset: 0; width: 100%; height: 100%; }

  /* brand name */
  .brand { display: flex; align-items: center; gap: 12px; }
  .brand-dot {
    width: 18px; height: 18px;
    border-radius: 50%;
    background: var(--blue);
  }
  .brand-name {
    font-weight: 600;
    color: var(--grey);
    letter-spacing: -0.5px;
    line-height: 1;
  }

  /* back */
  .back-brand {
    position: absolute;
    left: 0; right: 0; top: 128px;
  }
  .back-brand .brand { justify-content: center; }
  .back-brand .brand-dot { width: 30px; height: 30px; }
  .back-brand .brand-name { font-size: 46px; }
  .back-url {
    position: absolute;
    left: 28px; bottom: 9px;
    color: var(--white);
    font-size: 14px;
    font-weight: 500;
    letter-spacing: 0.2px;
  }

  /* front */
  .front-brand { position: absolute; left: 40px; top: 104px; }
  .front-brand .brand-name { font-size: 34px; }

  .person {
    position: absolute;
    right: 30px; top: 150px;
    text-align: right;
  }
  .person-name {
    color: var(--blue);
    font-size: 24px;
    font-weight: 700;
    line-height: 1.1;
  }
  .person-role {
    color: var(--grey-text);
    font-size: 13px;
    line-height: 1.3;
  }
  .person-address {
    position: absolute;
    right: 30px; top: 214px;
    text-align: right;
    color: var(--grey-text);
    font-size: 15px;
    line-height: 1.3;
  }
  .contact-list {
    position: absolute;
    left: 190px; top: 214px;
    list-style: none;
    color: var(--grey-text);
    font-size: 15px;
    line-height: 21px;
  }
  .contact-list li { display: flex; align-items: center; gap: 10px; }
  .contact-list svg { width: 12px; height: 12px; fill: var(--grey-text); flex: none; }
  .contact-list .url-strong { color: var(--blue); font-weight: 600; }
</style>
</head>
<body>

<section class="card card-back" aria-label="Card back">
  <svg class="bands" viewBox="0 0 640 366" preserveAspectRatio="none" aria-hidden="true">
    <polygon points="300,350 640,350 640,366 300,366" fill="var(--grey)"/>
    <polygon points="0,330 290,330 312,366 0,366" fill="var(--blue)"/>
  </svg>
  <div class="back-brand">
    <div class="brand">
      <span class="brand-dot"></span>
      <span class="brand-name">brightpath</span>
    </div>
  </div>
  <div class="back-url">www.brightpathlabs.com</div>
</section>

<section class="card card-front" aria-label="Card front">
  <svg class="bands" viewBox="0 0 640 366" preserveAspectRatio="none" aria-hidden="true">
    <line x1="190" y1="204" x2="610" y2="204" stroke="var(--blue)" stroke-width="1.5"/>
    <polygon points="0,348 470,348 470,366 0,366" fill="var(--grey-light)"/>
    <polygon points="478,268 640,268 640,366 458,366" fill="var(--blue)"/>
  </svg>

  <div class="front-brand">
    <div class="brand">
      <span class="brand-dot"></span>
      <span class="brand-name">brightpath</span>
    </div>
  </div>

  <div class="person">
    <div class="person-name">Marten Hale</div>
    <div class="person-role">Director</div>
  </div>
  <div class="person-address">
    PO Box 317 Eastvale<br>NSW Australia 2150
  </div>

  <ul class="contact-list">
    <li>
      <svg viewBox="0 0 24 24"><path d="M6.6 10.8a15.1 15.1 0 0 0 6.6 6.6l2.2-2.2c.3-.3.7-.4 1-.2 1.1.4 2.3.6 3.6.6.6 0 1 .4 1 1V20c0 .6-.4 1-1 1A17 17 0 0 1 3 4c0-.6.4-1 1-1h3.5c.6 0 1 .4 1 1 0 1.3.2 2.5.6 3.6.1.3 0 .7-.2 1z"/></svg>
      +330 4810-2297
    </li>
    <li>
      <svg viewBox="0 0 24 24"><rect x="5" y="3" width="14" height="6"/><rect x="3" y="10" width="18" height="8" rx="1"/><rect x="7" y="15" width="10" height="6"/></svg>
      +330 4810-3358
    </li>
    <li>
      <svg viewBox="0 0 24 24"><path d="M2 5h20v14H2z M4 7v1l8 5 8-5V7l-8 5z" fill-rule="evenodd"/></svg>
      info@brightpathlabs.com
    </li>
    <li>
      <svg viewBox="0 0 24 24"><circle cx="12" cy="12" r="10"/></svg>
      <span>www.<span class="url-strong">brightpathlabs</span>.com</span>
    </li>
  </ul>
</section>

</body>
</html>
```